General Surgeon flyer to be distributed to GPs

I am a general surgeon and I would like to have a flyer designed aiming to introduce myself to GPs.

Name: Dr Tobias Lindqvar MD, FRACS
Address: Suite 4C, Brellam private hospital, 418 Corvell Parade, Haldenby, NSW, 2794
T: (03) 9587 6102
F: (03) 9463 1178
E: referrals@quillfordsurgeons.com.au
Website: www.quillfordsurgeons.com.au

Tobias is a highly trained general surgeon, having completed extensive surgical training at Tarrowby health, Pellington and Corrigan Health networks. He further specialized by completing a fellowship in Oesophagogastric and Bariatric Surgery at St Aldric’s Hospital Melbourne, one of Victoria’s leading Upper GI surgical centres.

With expertise in both advanced laparoscopic and open surgical techniques, he performs a wide range of procedures involving the gastrointestinal system, abdominal wall hernias, as well as other major and minor general surgical operations. In addition to holding appointments at Tarrowby Health, he also operates at Brellam and Fernwick Private Hospitals.

Dr Lindqvar is committed to providing patient-centred care with a focus on surgical precision, safety, and long-term health outcomes.

He is also fluent in Farsi/Pesrian.
Outside of surgery, Tobias enjoys playings classical piano and spending time with his 6-year-old Bordoodle on long walks.

Upper GI & Bariatric Surgery:
Hiatus hernia repair, sleeve gastrectomy, gastric bypass
General Surgery conditions:
Gallbladder Surgery: Laparoscopic cholecystectomy
Hernia Repair: Laparoscopic and open surgery (inguinal,
umbilical, incisional)
Anorectal Procedures: Haemorrhoidectomy, haemorrhoid banding
Hand Surgery: Carpal tunnel release, Lymph Node Biopsy
Ingrown Toenail Surgery
Skin & Soft Tissue Surgery: Skin cancer removal, lipoma and
sebaceous cyst excision
Emergency Surgery: Laparotomy, Appendicectomy, bowel resection
Endoscopy: Diagnostic and therapeutic procedures

```html
<!DOCTYPE html>
<html lang="en">
<head>
<meta charset="utf-8">
<title>Dr Tobias Lindqvar – General Surgeon</title>
<link href="https://fonts.googleapis.com/css2?family=Poppins:wght@400;500;600;700&display=swap" rel="stylesheet">
<style>
  :root {
    --bg: #c2c2c2;
    --paper: #ffffff;
    --blue: #0fb9ee;
    --blue-deep: #0a9fd8;
    --green: #33c05a;
    --green-dark: #0c3a18;
    --ink: #1b1b1b;
    --ink-soft: #2a2a2a;
    --badge: #e8edf3;
  }
  * { margin: 0; padding: 0; box-sizing: border-box; }
  html, body { width: 1200px; height: 1200px; overflow: hidden; }
  body { background: var(--bg); font-family: "Poppins", sans-serif; color: var(--ink); }

  .flyer {
    position: absolute; left: 180px; top: 56px;
    width: 841px; height: 1088px;
    background: var(--paper); overflow: hidden;
  }
  .abs { position: absolute; }

  /* brand */
  .brand { left: 118px; top: 100px; display: flex; align-items: center; gap: 9px; }
  .brand-dot { width: 30px; height: 30px; border-radius: 50%; background: var(--green); }
  .brand-name { font-weight: 600; font-size: 19px; color: var(--blue-deep); line-height: 1.1; white-space: nowrap; }

  /* name */
  .doctor-name { left: 44px; top: 204px; font-size: 36px; font-weight: 400; letter-spacing: -0.5px; white-space: nowrap; line-height: 44px; }
  .doctor-name strong { font-weight: 700; }
  .credentials { left: 45px; top: 245px; font-size: 22px; letter-spacing: 6px; line-height: 30px; }
  .name-rule { left: 45px; top: 287px; width: 68px; height: 3px; background: var(--blue); }

  /* contact */
  .contact { left: 48px; font-size: 14.5px; color: var(--ink-soft); display: flex; align-items: flex-start; gap: 8px; line-height: 19px; white-space: nowrap; }
  .contact-icon { width: 20px; height: 20px; flex: none; margin-top: 0; }

  /* section bands */
  .band {
    left: 50px; width: 314px; height: 27px;
    background: var(--blue); color: #fff;
    border-radius: 0 14px 14px 0;
    font-weight: 700; font-size: 15.5px; line-height: 27px; padding-left: 19px; white-space: nowrap;
  }

  .gi-item { display: flex; align-items: center; gap: 6px; font-size: 12.5px; line-height: 15px; top: 532px; white-space: nowrap; }
  .gi-icon { width: 28px; height: 28px; border-radius: 50%; background: var(--green); border: 2px solid #9fe0b0; flex: none; }

  .cond { left: 57px; display: flex; gap: 7px; white-space: nowrap; }
  .cond-tick { width: 11px; height: 11px; margin-top: 4px; flex: none; }
  .cond h3 { font-size: 14.5px; font-weight: 700; color: var(--blue); line-height: 18px; }
  .cond p { font-size: 12.8px; line-height: 15px; color: var(--ink); }

  .sponsors-label { left: 48px; top: 1003px; font-weight: 700; font-size: 15.5px; line-height: 19px; }
  .sponsors-label span { color: var(--blue); display: block; }
  .badge-a { left: 162px; top: 1018px; width: 140px; height: 28px; background: var(--badge); border-radius: 4px; }
  .badge-b { left: 330px; top: 990px; width: 66px; height: 56px; background: var(--badge); border-radius: 50%; }

  /* right panel */
  .panel-art { left: 0; top: 0; width: 841px; height: 1088px; }
  .portrait { left: 467px; top: 87px; width: 310px; height: 310px; border-radius: 50%; border: 6px solid #fff;
    background: radial-gradient(circle at 50% 32%, #c9b29a 0 20%, #e2e2e2 21% 46%, #4a5f8e 47% 100%); }

  .bio { right: 53px; text-align: right; color: #fff; font-size: 12.4px; line-height: 14.9px; white-space: nowrap; }
  .bio b { font-weight: 600; }
  .bio .hl { color: var(--green-dark); }
  .bio-title { right: 53px; top: 790px; font-size: 18px; line-height: 22px; color: var(--green-dark); }
  .bio-title strong { font-weight: 700; }

  .focus { font-weight: 600; font-size: 12.4px; color: #fff; display: flex; align-items: center; gap: 5px; line-height: 15px; text-align: center; white-space: nowrap; }
  .focus-icon { width: 20px; height: 20px; border-radius: 50%; background: var(--green-dark); border: 1.5px solid #fff; flex: none; }

  .lang-box { left: 511px; top: 924px; width: 276px; height: 27px; background: var(--green-dark); color: #fff; border-radius: 3px;
    font-weight: 700; font-size: 14.5px; line-height: 27px; text-align: center; white-space: nowrap; }
  .website { right: 54px; top: 1026px; font-weight: 700; font-size: 14px; line-height: 18px; color: #fff; white-space: nowrap; }
  .website span { color: var(--green-dark); }
</style>
</head>
<body>
<main class="flyer">

  <!-- right panel shapes -->
  <svg class="abs panel-art" viewBox="0 0 841 1088" aria-hidden="true">
    <circle cx="640" cy="236" r="183" fill="var(--green)"/>
    <rect x="438" y="248" width="383" height="840" fill="var(--blue)"/>
    <circle cx="622" cy="248" r="184" fill="var(--blue)"/>
    <path d="M821 292 C790 360 740 395 702 410 C650 432 610 455 584 484 C540 525 505 560 488 620 C474 670 468 710 468 760 L468 1088 L821 1088 Z" fill="var(--green)"/>
    <!-- crosses -->
    <path d="M484 378 h30 v27 h28 v30 h-28 v27 h-30 v-27 h-26 v-30 h26 z" fill="none" stroke="#fff" stroke-width="3"/>
    <path d="M551 427 h16 v14 h14 v15 h-14 v14 h-16 v-14 h-14 v-15 h14 z" fill="#fff"/>
    <!-- stethoscope -->
    <g fill="none" stroke="#fff" stroke-width="3.5" stroke-linecap="round">
      <path d="M774 401 C762 405 762 425 767 438 C772 451 792 451 797 438 C802 425 802 405 790 401"/>
      <path d="M782 449 L782 456 C782 472 762 472 759 458 L759 446 C759 434 744 434 744 446"/>
      <circle cx="744" cy="452" r="8"/>
    </g>
  </svg>
  <div class="abs portrait" role="img" aria-label="Portrait photo of Dr Tobias Lindqvar in a suit"></div>

  <!-- brand -->
  <div class="abs brand">
    <div class="brand-dot"></div>
    <div class="brand-name">Quillford Surgeons</div>
  </div>

  <h1 class="abs doctor-name">Dr <strong>Tobias Lindqvar</strong></h1>
  <div class="abs credentials">MD, FRACS</div>
  <div class="abs name-rule"></div>

  <!-- contact -->
  <div class="abs contact" style="top:321px">
    <svg class="contact-icon" viewBox="0 0 22 22"><circle cx="11" cy="11" r="11" fill="var(--green)"/><path d="M11 5a4 4 0 0 1 4 4c0 3-4 8-4 8s-4-5-4-8a4 4 0 0 1 4-4z" fill="#fff"/><circle cx="11" cy="9" r="1.5" fill="var(--green)"/></svg>
    <div>Suite 4C, Brellam private hospital, 418<br>Corvell Parade, Haldenby, NSW, 2794</div>
  </div>
  <div class="abs contact" style="top:371px">
    <svg class="contact-icon" viewBox="0 0 22 22"><circle cx="11" cy="11" r="11" fill="var(--green)"/><path d="M7 6l3 0 1 3-2 1.5a7 7 0 0 0 3 3L13.5 12l3 1v3c-5 0-9.5-4.5-9.5-10z" fill="#fff"/></svg>
    <div>(03) 9587 6102</div>
  </div>
  <div class="abs contact" style="top:404px">
    <svg class="contact-icon" viewBox="0 0 22 22"><circle cx="11" cy="11" r="11" fill="var(--green)"/><rect x="6" y="8" width="10" height="8" rx="1" fill="#fff"/><rect x="8" y="5" width="6" height="4" fill="#fff"/></svg>
    <div>(03) 9463 1178</div>
  </div>
  <div class="abs contact" style="top:440px">
    <svg class="contact-icon" viewBox="0 0 22 22"><circle cx="11" cy="11" r="11" fill="var(--green)"/><rect x="5.5" y="7" width="11" height="8" fill="#fff"/><path d="M5.5 7l5.5 4.5L16.5 7" fill="none" stroke="var(--green)" stroke-width="1"/></svg>
    <div>referrals@quillfordsurgeons.com.au</div>
  </div>

  <!-- upper GI -->
  <div class="abs band" style="top:484px">UPPER GI &amp; BARIATRIC SURGERY</div>
  <div class="abs gi-item" style="left:48px"><div class="gi-icon"></div><div>Hiatus<br>hernia repair</div></div>
  <div class="abs gi-item" style="left:176px"><div class="gi-icon"></div><div>Sleeve<br>gastrectomy</div></div>
  <div class="abs gi-item" style="left:305px"><div class="gi-icon"></div><div>Gastric<br>bypass</div></div>

  <!-- general surgery -->
  <div class="abs band" style="top:591px">GENERAL SURGERY CONDITIONS</div>

  <div class="abs cond" style="top:636px"><svg class="cond-tick" viewBox="0 0 14 14"><circle cx="7" cy="7" r="7" fill="var(--green)"/><path d="M4 7.2l2 2 4-4.2" fill="none" stroke="#fff" stroke-width="1.6"/></svg><div><h3>Gallbladder Surgery</h3><p>Laparoscopic cholecystectomy</p></div></div>
  <div class="abs cond" style="top:680px"><svg class="cond-tick" viewBox="0 0 14 14"><circle cx="7" cy="7" r="7" fill="var(--green)"/><path d="M4 7.2l2 2 4-4.2" fill="none" stroke="#fff" stroke-width="1.6"/></svg><div><h3>Hernia Repair</h3><p>Laparoscopic and open surgery<br>(inguinal, umbilical, incisional)</p></div></div>
  <div class="abs cond" style="top:740px"><svg class="cond-tick" viewBox="0 0 14 14"><circle cx="7" cy="7" r="7" fill="var(--green)"/><path d="M4 7.2l2 2 4-4.2" fill="none" stroke="#fff" stroke-width="1.6"/></svg><div><h3>Anorectal Procedures</h3><p>Haemorrhoidectomy, haemorrhoid banding</p></div></div>
  <div class="abs cond" style="top:783px"><svg class="cond-tick" viewBox="0 0 14 14"><circle cx="7" cy="7" r="7" fill="var(--green)"/><path d="M4 7.2l2 2 4-4.2" fill="none" stroke="#fff" stroke-width="1.6"/></svg><div><h3>Hand Surgery</h3><p>Carpal tunnel release, Lymph Node Biopsy<br>Ingrown Toenail Surgery</p></div></div>
  <div class="abs cond" style="top:843px"><svg class="cond-tick" viewBox="0 0 14 14"><circle cx="7" cy="7" r="7" fill="var(--green)"/><path d="M4 7.2l2 2 4-4.2" fill="none" stroke="#fff" stroke-width="1.6"/></svg><div><h3>Skin &amp; Soft Tissue Surgery</h3><p>Skin cancer removal, lipoma and<br>sebaceous cyst excision</p></div></div>
  <div class="abs cond" style="top:903px"><svg class="cond-tick" viewBox="0 0 14 14"><circle cx="7" cy="7" r="7" fill="var(--green)"/><path d="M4 7.2l2 2 4-4.2" fill="none" stroke="#fff" stroke-width="1.6"/></svg><div><h3>Emergency Surgery</h3><p>Laparotomy, Appendicectomy, bowel resection</p></div></div>
  <div class="abs cond" style="top:948px"><svg class="cond-tick" viewBox="0 0 14 14"><circle cx="7" cy="7" r="7" fill="var(--green)"/><path d="M4 7.2l2 2 4-4.2" fill="none" stroke="#fff" stroke-width="1.6"/></svg><div><h3>Endoscopy</h3><p>Diagnostic and therapeutic procedures</p></div></div>

  <!-- sponsors -->
  <div class="abs sponsors-label">OUR<span>SPONSORS</span></div>
  <div class="abs badge-a" role="img" aria-label="Professional college badge"></div>
  <div class="abs badge-b" role="img" aria-label="Professional society badge"></div>

  <!-- bio -->
  <p class="abs bio" style="top:485px">
    <b><span class="hl">Tobias</span> is a highly trained<br>general surgeon, having<br>completed extensive surgical<br>training at Tarrowby health,<br>Pellington and Corrigan Health networks.</b><br>
    He further specialized by completing<br>a fellowship in Oesophagogastric and<br>Bariatric Surgery at St Aldric’s Hospital<br>Melbourne, one of Victoria’s leading Upper<br>GI surgical centres.
  </p>
  <p class="abs bio" style="top:645px">
    With expertise in both advanced laparoscopic<br>and open surgical techniques, he performs a<br>wide range of procedures involving the<br>gastrointestinal system, abdominal wall<br>hernias, as well as other major and minor<br>general surgical operations. In addition to<br>holding appointments at Tarrowby Health,<br>he also operates at Brellam and Fernwick<br>Private Hospitals.
  </p>

  <div class="abs bio-title">DR <strong>LINDQVAR</strong></div>
  <p class="abs bio" style="top:816px">Is committed to providing patient-centred<br>care with a focus on</p>

  <div class="abs focus" style="right:204px; top:863px">Surgical precision <div class="focus-icon"></div></div>
  <div class="abs focus" style="right:204px; top:887px">Safety <div class="focus-icon"></div></div>
  <div class="abs focus" style="right:52px; top:863px"><div>Long-term<br>health<br>outcomes</div><div class="focus-icon" style="align-self:flex-start"></div></div>

  <div class="abs lang-box">He is also fluent in Farsi/Pesrian</div>
  <p class="abs bio" style="top:961px; right:54px">Outside of surgery, Tobias enjoys playings<br>classical piano and spending time with his<br><b>6-year-old Bordoodle on long walks.</b></p>

  <div class="abs website">www.<span>quillfordsurgeons</span>.com.au</div>
</main>
</body>
</html>
```